Very new and innovative Web design for Property managers of Vacation rentals

We are looking for a new website design for travel agencies and property managers specialised on vacation rentals business, holiday villas and apartments.

The end users of this website are travellers who are looking for a vacation home for their next holiday: this is the reason why the website must be easy to use, attractive, professional, possibly elegant and focused on get new reservations.

This is a draft of our current website: https://intro3.kelumsito.com/
Please consider that we would like to have proposals with a totally different and innovative layout, surprise us!

These are the pages of the website:
• Homepage: feel free to redesign all the homepage as you wish, surprise us with something very new! Please consider that Property manager/Travel agencies usually want to have the opportunity to put in evidence groups of houses with specific characteristics (eg. villas with private swimming pool, apartment in big/small towns, villas with air co, etc…), destinations and tourist areas, and sometimes experiences or activities (please consider that the website layout must be suitable even if some of the previous sections are not used).
• Search page: we’d like to organise the results of the search page in three different ways:
o Grid
o Map
o List
• Property page: to illustrate the characteristics, descriptions, images, …. of the property. It is very important to put in evidence images of the property and to maintain the booking form (and the other call to action bottom – eg. whatsapp) always visible
• Custom pages: static pages composed usually by text, images and call to actions
• Contact us (general form)
• Info request (specific of a property form)
• Booking process
• Blog, organised in four pages:
o Home Page – introduction to the blog
o List of articles
o Single article
o Site Map (presentation of categories and sub-categories)

If possible, we’d prefer to receive the material in Adobe XD or similar so that we can obtain the three versions:
- smartphone
- tablet
- desktop

The website will be then developed in Bootstrap: as a result we’ll need the icons in SVG format (or the library used)

In attachment you can find the map of the website pages

```html
<!DOCTYPE html>
<html lang="en">
<head>
<meta charset="utf-8">
<title>StayNest – Blog Details</title>
<link href="https://fonts.googleapis.com/css2?family=Oswald:wght@300;400;500&family=Poppins:wght@300;400;500;600&display=swap" rel="stylesheet">
<style>
:root{
  --green:#0db58c;
  --ink:#1e1e1e;
  --muted:#6b6b6b;
  --line:#e2e2e2;
  --footer:#1b1a1a;
  --white:#fff;
}
*{box-sizing:border-box;margin:0;padding:0}
html,body{width:1200px;height:2276px;overflow:hidden;background:var(--white);font-family:'Poppins',sans-serif;color:var(--ink)}
.page{position:relative;width:1200px;height:2276px}
.abs{position:absolute}
.heading{font-family:'Oswald',sans-serif;font-weight:300;text-transform:uppercase;letter-spacing:-.2px}

/* header */
.brand{left:97px;top:22px;display:flex;align-items:center;gap:8px;font-size:24px;font-weight:400;color:#555}
.brand .dot{width:26px;height:26px;border-radius:50%;background:var(--green)}
.brand b{font-weight:400;color:var(--green)}
.topbar{left:870px;top:0;width:330px;height:32px;background:var(--green);clip-path:polygon(0 0,100% 0,100% 100%,30px 100%);display:flex;align-items:center;justify-content:flex-end;gap:22px;padding-right:36px;color:#fff;font-size:10px;font-weight:600}
.topbar span{display:flex;align-items:center;gap:4px}
.nav{top:48px;font-size:11.5px;color:#333}
.nav.active{color:var(--green);font-weight:500}

/* hero */
.hero{left:0;top:93px;width:1200px;height:244px;background:linear-gradient(90deg,#7d7263 0%,#5c6660 30%,#35505f 55%,#2a4656 100%)}
.hero-title{left:0;top:238px;width:1200px;text-align:center;color:#fff;font-family:'Oswald',sans-serif;font-weight:500;font-size:38px;letter-spacing:-.5px}

.crumbs{left:93px;top:371px;font-size:11px;color:#777}
.crumbs .cur{color:#222}

/* article */
.photo{left:94px;top:442px;width:731px;height:438px;border-radius:8px;background:linear-gradient(120deg,#7a3a2c 0%,#b88a55 40%,#d8c7a2 65%,#6d6a64 100%)}
.meta{left:94px;top:915px;font-size:11.5px;color:#222;word-spacing:1px}
.post-title{left:94px;top:945px;font-family:'Oswald',sans-serif;font-weight:300;font-size:22px;color:#222}
.post-body{left:94px;top:985px;width:736px;font-size:12.4px;line-height:20.3px;color:#707070;font-weight:300;letter-spacing:-.15px}
.shares{left:94px;top:1152px;display:flex;gap:4px}
.shares span{width:27px;height:27px;border:1px solid var(--line);display:flex;align-items:center;justify-content:center}

/* sidebar */
.box{left:900px;width:206px;border:1px solid var(--line)}
.box h3{position:absolute;left:14px;top:14px;font-size:18px;color:#222}
.cats{top:441px;height:414px}
.cat{position:absolute;left:14px;width:170px;font-size:12.4px;color:#222;display:flex;justify-content:space-between}
.searchbox{top:885px;height:108px}
.field-search{position:absolute;left:12px;top:53px;width:182px;height:31px;border:1px solid #bbb;border-radius:6px;font-size:10.5px;color:#888;padding:8px 10px}
.tags{top:1023px;height:164px}
.tag{position:absolute;width:58px;height:28px;border:1px solid var(--line);font-size:9px;color:#444;display:flex;align-items:center;justify-content:center}

/* comment form */
.comment-h{left:94px;top:1264px;font-size:19px;color:#222}
.input{border:1px solid #ddd;font-size:9.5px;color:#555;padding:10px 7px}
.check{left:94px;top:1367px;font-size:10.5px;color:#888;display:flex;align-items:center;gap:4px;font-weight:300}
.check i{width:12px;height:12px;border:1px solid #ccc}
.btn{left:94px;top:1560px;width:112px;height:39px;background:var(--green);color:#fff;font-size:10px;display:flex;align-items:center;justify-content:center}

/* footer */
.footer{left:0;top:1665px;width:1200px;height:611px;background:var(--footer)}
.f-brand{left:96px;top:1757px;display:flex;align-items:center;gap:8px;font-size:25px;font-weight:500;color:#fff;letter-spacing:1.5px}
.f-brand .dot{width:28px;height:28px;border-radius:50%;background:var(--green)}
.f-h{font-size:14.5px;font-weight:500;color:var(--green);letter-spacing:1.5px}
.f-link{font-size:12.4px;color:#eee;letter-spacing:1.2px}
.thumb{width:70px;height:60px}
.rp-title{font-size:12px;font-weight:600;color:var(--green);letter-spacing:.2px;line-height:15px;width:230px}
.rp-date{font-size:12px;color:#ddd;letter-spacing:.2px}
.c-h{font-size:14.5px;font-weight:600;color:var(--green);letter-spacing:1.3px}
.c-t{font-size:14.5px;color:#fff;letter-spacing:1.3px}
.vline{width:1px;background:#333;top:2002px;height:119px}
</style>
</head>
<body>
<div class="page">

  <!-- header -->
  <div class="abs brand"><span class="dot"></span><span><b>StayNest</b></span></div>
  <div class="abs topbar">
    <span><svg width="11" height="11" viewBox="0 0 12 12" fill="none" stroke="#fff" stroke-width="1.2"><circle cx="6" cy="4" r="2.5"/><path d="M1.5 11.5c0-2.5 2-4 4.5-4s4.5 1.5 4.5 4"/></svg>LOGIN</span>
    <span><svg width="12" height="11" viewBox="0 0 12 11" fill="none" stroke="#fff" stroke-width="1.2"><path d="M6 10 1.5 5.5A2.5 2.5 0 0 1 6 2a2.5 2.5 0 0 1 4.5 3.5Z"/></svg>WHISHLIST</span>
    <span>EN ˅</span>
  </div>
  <div class="abs nav active" style="left:660px">HOME</div>
  <div class="abs nav" style="left:741px">SEARCH</div>
  <div class="abs nav" style="left:833px">PROPERTY</div>
  <div class="abs nav" style="left:938px">CUSTOM</div>
  <div class="abs nav" style="left:1033px">CONTACT US</div>

  <!-- hero -->
  <div class="abs hero" role="img" aria-label="Seaside villa on a cliff with a yacht on the calm sea"></div>
  <div class="abs hero-title">BLOG DETAILS</div>

  <div class="abs crumbs">Home &nbsp;/&nbsp; Blog &nbsp;/&nbsp; <span class="cur">Blog Details</span></div>

  <!-- article -->
  <div class="abs photo" role="img" aria-label="Guest checking in at a hotel reception desk"></div>
  <div class="abs meta">Jhon Doe &nbsp;&nbsp; | &nbsp;&nbsp; December 4, 2020 &nbsp;&nbsp; | &nbsp;&nbsp; 0 Comments</div>
  <div class="abs post-title">One who avoids a pain that produces no resultant pleasure</div>
  <p class="abs post-body">Sed ut perspiciatis unde omnis iste natus error sit voluptatem accusantium doloremque laudantium, totam rem aperiam, eaque ipsa quae ab illo inventore veritatis et quasi architecto beatae vitae dicta sunt explicabo. Nemo enim ipsam voluptatem quia voluptas sit aspernatur aut odit aut fugit, sed quia consequuntur magni dolores eos qui ratione voluptatem sequi nesciunt. Neque porro quisquam est, qui dolorem ipsum quia dolor sit amet, consectetur, adipisci velit, sed quia non numquam eius modi tempora incidunt ut labore et dolore magnam aliquam quaerat voluptatem. Ut enim ad minima veniam, quis nostrum exercitationem ullam corporis suscipit laboriosam, nisi ut aliquid ex ea commodi consequatur</p>
  <div class="abs shares" aria-label="Share options">
    <span><svg width="11" height="11" viewBox="0 0 12 12" fill="none" stroke="#333" stroke-width="1.2"><circle cx="9.5" cy="2.5" r="1.5"/><circle cx="2.5" cy="6" r="1.5"/><circle cx="9.5" cy="9.5" r="1.5"/><path d="M4 5.2 8 3.3M4 6.8 8 8.7"/></svg></span>
    <span><svg width="11" height="11" viewBox="0 0 12 12" fill="none" stroke="#333" stroke-width="1.2"><path d="M5 7 7 5M4.5 5.5 3 7a2 2 0 0 0 2.8 2.8L7.3 8.3M7.5 6.5 9 5a2 2 0 0 0-2.8-2.8L4.7 3.7"/></svg></span>
    <span><svg width="11" height="11" viewBox="0 0 12 12" fill="none" stroke="#333" stroke-width="1.2"><rect x="1" y="2.5" width="10" height="7" rx="1"/><path d="m1.5 3 4.5 3.5L10.5 3"/></svg></span>
    <span><svg width="11" height="11" viewBox="0 0 12 11" fill="none" stroke="#333" stroke-width="1.2"><path d="M6 10 1.5 5.5A2.5 2.5 0 0 1 6 2a2.5 2.5 0 0 1 4.5 3.5Z"/></svg></span>
    <span><svg width="11" height="11" viewBox="0 0 12 12" fill="none" stroke="#333" stroke-width="1.2"><path d="M3 1.5h6v9L6 8l-3 2.5Z"/></svg></span>
    <span><svg width="11" height="11" viewBox="0 0 12 12" fill="none" stroke="#333" stroke-width="1.2"><rect x="3" y="5" width="6" height="5.5" rx=".5"/><path d="M4 5V3h4v2M2 7h1M9 7h1"/></svg></span>
  </div>

  <!-- sidebar -->
  <div class="abs box cats">
    <h3 class="heading">Categories</h3>
    <div class="cat" style="top:65px">Consectetur Adipiscing<span>+</span></div>
    <div class="cat" style="top:100px">Eget Tempor<span>+</span></div>
    <div class="cat" style="top:135px">Lobortis Dictum<span>+</span></div>
    <div class="cat" style="top:171px">Tempus Fermentum<span>+</span></div>
    <div class="cat" style="top:206px">Quisque<span>+</span></div>
    <div class="cat" style="top:241px">Consectetur Adipiscing<span>+</span></div>
    <div class="cat" style="top:276px">Eget Tempor<span>+</span></div>
    <div class="cat" style="top:312px">Lobortis Dictum<span>+</span></div>
    <div class="cat" style="top:347px">Tempus Fermentum<span>+</span></div>
    <div class="cat" style="top:382px">Quisque<span>+</span></div>
  </div>
  <div class="abs box searchbox">
    <h3 class="heading">Search</h3>
    <div class="field-search">Search here
      <svg style="position:absolute;right:10px;top:9px" width="12" height="12" viewBox="0 0 12 12" fill="none" stroke="#222" stroke-width="1.4"><circle cx="5" cy="5" r="4"/><path d="m8 8 3 3"/></svg>
    </div>
  </div>
  <div class="abs box tags">
    <h3 class="heading">Popular Tags</h3>
    <div class="tag" style="left:12px;top:51px">AGENCY</div>
    <div class="tag" style="left:73px;top:51px">BUSINESS</div>
    <div class="tag" style="left:134px;top:51px">CLEAN</div>
    <div class="tag" style="left:12px;top:84px">CREATIVE</div>
    <div class="tag" style="left:73px;top:84px">DESIGN</div>
    <div class="tag" style="left:134px;top:84px">MODERN</div>
    <div class="tag" style="left:12px;top:118px">POPULAR</div>
  </div>

  <!-- comment form -->
  <div class="abs heading comment-h">Leave Comment</div>
  <div class="abs input" style="left:94px;top:1310px;width:204px;height:33px">Your Name:</div>
  <div class="abs input" style="left:305px;top:1310px;width:205px;height:33px">Email:</div>
  <div class="abs check"><i></i>Save my name, email, and website in this browser for the next time I comment.</div>
  <div class="abs input" style="left:94px;top:1402px;width:204px;height:34px">Phone:</div>
  <div class="abs input" style="left:305px;top:1402px;width:205px;height:34px">Website:</div>
  <div class="abs input" style="left:94px;top:1450px;width:416px;height:101px">Comments:</div>
  <div class="abs btn">Post Comments</div>

  <!-- footer -->
  <div class="abs footer"></div>
  <div class="abs f-brand"><span class="dot"></span>StayNest</div>
  <div class="abs f-link" style="left:95px;top:1826px;font-weight:500">Subscribe to our Newsletter</div>
  <div class="abs" style="left:95px;top:1849px;width:210px;height:2px;background:#fff"></div>
  <svg class="abs" style="left:325px;top:1843px" width="40" height="12" viewBox="0 0 40 12" fill="none" stroke="#0db58c" stroke-width="1.4"><path d="M0 6h38M33 1l5 5-5 5"/></svg>
  <p class="abs f-link" style="left:95px;top:1874px;width:310px;line-height:18px">Our range of services is very large, and we are constantly expanding it.</p>

  <div class="abs f-h" style="left:516px;top:1739px">Navigation</div>
  <div class="abs f-link" style="left:518px;top:1778px">Last Minute</div>
  <div class="abs f-link" style="left:518px;top:1813px">Special Offers</div>
  <div class="abs f-link" style="left:518px;top:1847px">Experience</div>
  <div class="abs f-link" style="left:518px;top:1882px">Contact Us</div>

  <div class="abs f-h" style="left:791px;top:1739px">Recent posts</div>
  <div class="abs thumb" style="left:791px;top:1781px;background:linear-gradient(180deg,#6e8a5a,#3e9ed0)" role="img" aria-label="Villa garden with a swimming pool"></div>
  <div class="abs rp-title" style="left:872px;top:1779px">Which construction tool is better to choose?</div>
  <div class="abs rp-date" style="left:872px;top:1823px">2 November, 2020</div>
  <div class="abs thumb" style="left:791px;top:1866px;background:linear-gradient(180deg,#6f5a48,#4d7fb8)" role="img" aria-label="Games room with a table tennis table"></div>
  <div class="abs rp-title" style="left:872px;top:1864px">Which construction tool is better to choose?</div>
  <div class="abs rp-date" style="left:872px;top:1908px">2 November, 2020</div>

  <svg class="abs" style="left:121px;top:2026px" width="30" height="30" viewBox="0 0 24 24" fill="none" stroke="#0db58c" stroke-width="2"><path d="M5 3h4l2 5-2.5 1.5a11 11 0 0 0 6 6L16 13l5 2v4a2 2 0 0 1-2 2A17 17 0 0 1 3 5a2 2 0 0 1 2-2"/></svg>
  <div class="abs c-h" style="left:165px;top:2027px">Call us</div>
  <div class="abs c-t" style="left:165px;top:2045px">+1 555 010 4477 (USA)</div>
  <div class="abs vline" style="left:434px"></div>
  <svg class="abs" style="left:484px;top:2027px" width="42" height="30" viewBox="0 0 42 30" fill="none" stroke="#0db58c" stroke-width="2"><rect x="1" y="1" width="40" height="28" rx="3"/><path d="m2 3 19 14L40 3"/></svg>
  <div class="abs c-h" style="left:536px;top:2027px">Write to us</div>
  <div class="abs c-t" style="left:536px;top:2045px">sales@example.com</div>
  <div class="abs vline" style="left:764px"></div>
  <svg class="abs" style="left:823px;top:2022px" width="32" height="42" viewBox="0 0 32 42" fill="none" stroke="#0db58c" stroke-width="2"><path d="M16 41S2 25 2 15a14 14 0 0 1 28 0c0 10-14 26-14 26Z"/><circle cx="16" cy="15" r="5"/></svg>
  <div class="abs c-h" style="left:860px;top:2027px">Office location</div>
  <div class="abs c-t" style="left:860px;top:2045px">12 Harbor Lane, Bayview, NY 11000</div>
  <div class="abs" style="left:95px;top:2123px;width:1011px;height:1px;background:#333"></div>

  <div class="abs f-link" style="left:0;top:2148px;width:1200px;text-align:center;font-weight:500">Privacy Policies &nbsp;&nbsp;/&nbsp;&nbsp; Reservation Policies &nbsp;&nbsp;/&nbsp;&nbsp; Cookie Policy</div>
  <div class="abs f-link" style="left:0;top:2166px;width:1200px;text-align:center;font-weight:500">Copyright © 2021 StayNest. All Rights Reserved. <span style="color:var(--green)">Powered by StayNest</span></div>
  <div class="abs" style="left:578px;top:2203px;width:16px;height:16px;border-radius:50%;background:#fff"></div>
  <div class="abs" style="left:599px;top:2205px;width:56px;height:13px;border-radius:2px;background:#4267b2"></div>

</div>
</body>
</html>
```